Velvet Circle club

We are looking to redesign the user interface of our mobile app “Velvet Circle”, which is the official rewards program for our luxury casino brand, Kestrane Harbour.
Our goal is to give the app a more elegant, premium, and user-friendly design that reflects the exclusivity of our brand and the luxury experience we offer our VIP clientele.
What We Need:
A complete UI design for the app’s main screens, including:
Splash Screen
01 Login / Signup Screen
02 Home Dashboard
Buttons -
Home / my card / my wallet / my booking / my host
My wallet / my offer / lucky game / my taxi / entertainment / online
03 Profile screen
04 My wallet
05 My offer
06Packages
07 My booking
08 My host
09 My card
we attached our privies app all the screen for you reference
Inspiration:
Think of luxury brands like Dunmore-Vale, Corvix Onyx, or high-end lifestyle apps. Clean interfaces, classy animations, and a sense of exclusivity are key.
We’re excited to see fresh, innovative takes that elevate the app to a truly world-class luxury experience for our users.
Thank you!
Casino

```html
<!DOCTYPE html>
<html lang="en">
<head>
<meta charset="utf-8">
<title>Velvet Circle club – App Screens</title>
<link href="https://fonts.googleapis.com/css2?family=Montserrat:wght@400;500;600;700&display=swap" rel="stylesheet">
<style>
:root{
  --page:#ffffff;
  --black:#050505;
  --panel:#2c2c2e;
  --card:#3a3a3c;
  --line:#5c5c60;
  --orange:#f6a623;
  --orange-deep:#e8931a;
  --white:#ffffff;
  --red:#e0262a;
}
*{box-sizing:border-box;margin:0;padding:0}
html,body{width:1200px;height:845px;overflow:hidden;background:var(--page);font-family:"Montserrat",sans-serif}
.canvas{position:relative;width:1200px;height:845px}
.screen{position:absolute;top:8px;width:382px;height:827px;overflow:hidden}
.screen--login{left:12px;background:var(--black)}
.screen--home{left:407px;background:var(--panel)}
.screen--gaming{left:804px;background:var(--panel)}

/* login */
.brand{position:absolute;top:58px;left:0;width:100%;text-align:center}
.brand__dot{width:46px;height:46px;border-radius:50%;background:var(--red);margin:0 auto 14px}
.brand__name{color:var(--orange);font-weight:700;font-size:26px;line-height:30px;letter-spacing:.5px}
.login-box{position:absolute;left:21px;width:341px;border:2px solid var(--line);border-radius:22px;color:var(--white)}
.login-box--member{top:244px;height:142px;border-color:var(--orange-deep)}
.login-box--new{top:401px;height:142px}
.login-box--temp{top:604px;height:131px;text-align:center}
.login-box__title{position:absolute;left:17px;top:22px;font-size:17px;font-weight:600;letter-spacing:.3px}
.login-box--member .login-box__title{color:var(--orange)}
.login-box__text{position:absolute;left:19px;top:56px;width:190px;font-size:12.5px;line-height:22px}
.login-box--temp .login-box__text{position:static;width:auto;padding-top:22px}
.pill{position:absolute;left:214px;top:49px;width:109px;height:42px;border-radius:21px;border:2px solid var(--white);color:var(--white);font-size:13px;font-weight:600;display:flex;align-items:center;justify-content:center}
.pill--orange{border-color:var(--orange-deep);color:var(--orange)}
.login-box--temp .pill{left:74px;top:62px;width:191px}
.or-divider{position:absolute;top:564px;width:100%;text-align:center;color:var(--white);font-size:17px;font-weight:600}

/* home */
.hero{position:absolute;top:0;left:0;width:382px;height:317px;border-radius:0 0 50% 50%/0 0 34px 34px;
  background:radial-gradient(ellipse at 50% 45%,#ffe9a8 0%,#d89a3a 18%,#3b3fc7 48%,#281a7a 75%,#1b124f 100%)}
.topbar-icon{position:absolute;top:34px}
.menu-grid{position:absolute;top:361px;left:22px;width:336px;height:340px}
.menu-tile{position:absolute;width:157px;height:84px;border:3px solid var(--orange);border-radius:20px;text-align:center;color:var(--orange);font-size:15px;font-weight:600;padding-top:16px}
.menu-tile__icon{position:absolute;left:50%;bottom:-16px;transform:translateX(-50%);width:54px;height:54px;border-radius:50%;background:var(--orange);box-shadow:0 0 0 5px var(--panel);display:flex;align-items:center;justify-content:center}
.bottom-nav{position:absolute;left:0;bottom:0;width:382px;height:53px;background:var(--black);display:flex;align-items:center}
.bottom-nav__item{flex:1;height:34px;display:flex;align-items:center;justify-content:center;border-right:1px solid #333}
.bottom-nav__item:last-child{border-right:none}
.bottom-nav__bump{position:absolute;left:50%;top:-22px;transform:translateX(-50%);width:86px;height:50px;border-radius:43px 43px 0 0;background:var(--black)}
.bottom-nav__center{position:absolute;left:50%;top:-14px;transform:translateX(-50%);width:56px;height:56px;border-radius:50%;border:3px solid var(--orange);display:flex;align-items:center;justify-content:center}

/* gaming */
.gaming-title{position:absolute;top:34px;width:100%;text-align:center;color:var(--orange);font-size:17px;font-weight:600}
.game-card{position:absolute;left:13px;width:355px;height:174px;background:var(--card);border:2px solid var(--line);border-radius:18px;overflow:hidden}
.game-card--active{border-color:var(--orange-deep)}
.game-card__photo{position:absolute;left:0;top:0;width:117px;height:100%}
.game-card__title{position:absolute;left:128px;top:9px;color:var(--orange);font-size:16px;font-weight:600}
.game-card__chev{position:absolute;right:14px;top:12px}
.game-card__text{position:absolute;left:128px;top:34px;width:212px;color:var(--white);font-size:12.2px;line-height:20.3px}
</style>
</head>
<body>
<div class="canvas">

  <!-- Login -->
  <section class="screen screen--login">
    <div class="brand">
      <div class="brand__dot"></div>
      <div class="brand__name">VELVET CIRCLE<br>CLUB</div>
    </div>
    <div class="login-box login-box--member">
      <h2 class="login-box__title">MEMBER LOGIN</h2>
      <p class="login-box__text">Now you can enjoy all the excitement of the casino right at your fingertips.</p>
      <span class="pill pill--orange">SIGN IN</span>
    </div>
    <div class="login-box login-box--new">
      <h2 class="login-box__title">NEW MEMBER LOGIN</h2>
      <p class="login-box__text">If you are a first time user, please go through the sign up process</p>
      <span class="pill">SIGN UP</span>
    </div>
    <div class="or-divider">-Or-</div>
    <div class="login-box login-box--temp">
      <p class="login-box__text">If you are with a temporary ID, sign in here</p>
      <span class="pill">TEMPORARY SIGN IN</span>
    </div>
  </section>

  <!-- Home -->
  <section class="screen screen--home">
    <div class="hero" role="img" aria-label="Bonus banner with slot machine reels and flying gold coins"></div>
    <svg class="topbar-icon" style="left:10px" width="32" height="24" viewBox="0 0 32 24"><g fill="#fff"><rect y="1" width="32" height="3.5" rx="1.7"/><rect y="10" width="32" height="3.5" rx="1.7"/><rect y="19" width="32" height="3.5" rx="1.7"/></g></svg>
    <svg class="topbar-icon" style="left:350px" width="24" height="26" viewBox="0 0 24 26"><path fill="#fff" d="M12 2a7 7 0 0 0-7 7v6l-3 4h20l-3-4V9a7 7 0 0 0-7-7zm-3 19a3 3 0 0 0 6 0z"/></svg>

    <div class="menu-grid">
      <div class="menu-tile" style="left:0;top:0">MY WALLET
        <span class="menu-tile__icon"><svg width="28" height="24" viewBox="0 0 28 24"><rect x="2" y="4" width="24" height="17" rx="3" fill="none" stroke="#2c2c2e" stroke-width="2.5"/><rect x="17" y="10" width="9" height="6" rx="2" fill="#2c2c2e"/></svg></span></div>
      <div class="menu-tile" style="left:179px;top:0">MY OFFER
        <span class="menu-tile__icon"><svg width="30" height="30" viewBox="0 0 30 30"><circle cx="15" cy="15" r="12" fill="none" stroke="#2c2c2e" stroke-width="2.5"/><path d="M10 20 20 10" stroke="#2c2c2e" stroke-width="2.5"/><circle cx="11" cy="11" r="2" fill="#2c2c2e"/><circle cx="19" cy="19" r="2" fill="#2c2c2e"/></svg></span></div>
      <div class="menu-tile" style="left:0;top:128px">LUCKY GAME
        <span class="menu-tile__icon"><svg width="32" height="32" viewBox="0 0 32 32"><circle cx="16" cy="16" r="13" fill="none" stroke="#2c2c2e" stroke-width="2.5"/><circle cx="16" cy="16" r="8" fill="none" stroke="#2c2c2e" stroke-width="2"/><text x="16" y="20.5" text-anchor="middle" font-family="Montserrat,sans-serif" font-size="12" font-weight="700" fill="#2c2c2e">7</text></svg></span></div>
      <div class="menu-tile" style="left:179px;top:128px">MY TAXI
        <span class="menu-tile__icon"><svg width="30" height="28" viewBox="0 0 30 28"><rect x="10" y="2" width="10" height="5" rx="1" fill="#2c2c2e"/><path d="M6 9h18l3 8v7H3v-7z" fill="#2c2c2e"/><rect x="8" y="11" width="14" height="5" fill="#f6a623"/><circle cx="8" cy="20" r="2" fill="#f6a623"/><circle cx="22" cy="20" r="2" fill="#f6a623"/></svg></span></div>
      <div class="menu-tile" style="left:0;top:256px">ENTERTAINMENT
        <span class="menu-tile__icon"><svg width="30" height="30" viewBox="0 0 30 30"><path fill="#2c2c2e" d="M15 3l3 7 7 .5-5.5 4.5 2 7-6.5-4-6.5 4 2-7L5 10.5l7-.5z"/><ellipse cx="15" cy="26" rx="10" ry="2.5" fill="none" stroke="#2c2c2e" stroke-width="2"/></svg></span></div>
      <div class="menu-tile" style="left:179px;top:256px">ONLINE
        <span class="menu-tile__icon"><svg width="30" height="26" viewBox="0 0 30 26"><rect x="5" y="3" width="20" height="14" rx="2" fill="#2c2c2e"/><path d="M2 20h26l-2 3H4z" fill="#2c2c2e"/><path d="M15 7l3 3-3 3-3-3z" fill="#f6a623"/></svg></span></div>
    </div>

    <nav class="bottom-nav">
      <span class="bottom-nav__bump"></span>
      <span class="bottom-nav__item"><svg width="30" height="26" viewBox="0 0 30 26"><path fill="#f6a623" d="M15 1 1 13h4v12h7v-8h6v8h7V13h4z"/></svg></span>
      <span class="bottom-nav__item"><svg width="32" height="30" viewBox="0 0 32 30"><circle cx="10" cy="6" r="5" fill="#f6a623"/><path d="M2 28v-9a7 7 0 0 1 14 0v9z" fill="#f6a623"/><rect x="15" y="15" width="16" height="11" rx="2" fill="#f6a623" stroke="#050505" stroke-width="1.5"/><rect x="15" y="18" width="16" height="2" fill="#050505"/></svg></span>
      <span class="bottom-nav__item"></span>
      <span class="bottom-nav__item"><svg width="30" height="30" viewBox="0 0 30 30"><rect x="2" y="4" width="26" height="24" rx="3" fill="#f6a623"/><rect x="2" y="10" width="26" height="2" fill="#050505"/><path d="M9 19l4 4 8-8" fill="none" stroke="#050505" stroke-width="2.5"/></svg></span>
      <span class="bottom-nav__item"><svg width="28" height="30" viewBox="0 0 28 30"><circle cx="14" cy="9" r="7" fill="#f6a623"/><path d="M2 29c0-8 5-12 12-12s12 4 12 12z" fill="#f6a623"/><path d="M5 10a9 9 0 0 1 18 0" fill="none" stroke="#f6a623" stroke-width="2"/></svg></span>
      <span class="bottom-nav__center"><svg width="28" height="24" viewBox="0 0 28 24"><rect x="1" y="3" width="26" height="19" rx="3" fill="#f6a623"/><rect x="17" y="9" width="10" height="7" rx="2" fill="#050505"/></svg></span>
    </nav>
  </section>

  <!-- Gaming -->
  <section class="screen screen--gaming">
    <svg style="position:absolute;left:8px;top:36px" width="14" height="22" viewBox="0 0 14 22"><path d="M12 2 3 11l9 9" fill="none" stroke="#f6a623" stroke-width="3"/></svg>
    <h1 class="gaming-title">GAMING</h1>
    <svg style="position:absolute;left:344px;top:34px" width="26" height="28" viewBox="0 0 24 26"><path fill="#f6a623" d="M12 2a7 7 0 0 0-7 7v6l-3 4h20l-3-4V9a7 7 0 0 0-7-7zm-3 19a3 3 0 0 0 6 0z"/></svg>

    <article class="game-card game-card--active" style="top:73px">
      <div class="game-card__photo" role="img" aria-label="Baccarat table with chip stack and playing cards" style="background:linear-gradient(160deg,#6a4a3a,#2f4a3c 55%,#1d2a24)"></div>
      <h2 class="game-card__title">BACCARAT</h2>
      <svg class="game-card__chev" width="10" height="16" viewBox="0 0 10 16"><path d="M2 2l6 6-6 6" fill="none" stroke="#f6a623" stroke-width="2.2"/></svg>
      <p class="game-card__text">Kestrane Baccarat is a very lucky game andeasy to play. It is the most popular card game in Asia and Kestrane Casino offers Baccarat Tables for All Players both High Stakes and Low stakes 24 hours</p>
    </article>
    <article class="game-card" style="top:259px">
      <div class="game-card__photo" role="img" aria-label="Roulette wheel on casino table" style="background:linear-gradient(170deg,#7a5a44,#5a2e1e 55%,#2a1a12)"></div>
      <h2 class="game-card__title">ROULETTE</h2>
      <svg class="game-card__chev" width="10" height="16" viewBox="0 0 10 16"><path d="M2 2l6 6-6 6" fill="none" stroke="#f6a623" stroke-width="2.2"/></svg>
      <p class="game-card__text">Kestrane Baccarat is a very lucky game andeasy to play. It is the most popular card game in Asia and Kestrane Casino offers Baccarat Tables for All Players both High Stakes and Low stakes 24 hours</p>
    </article>
    <article class="game-card" style="top:446px">
      <div class="game-card__photo" role="img" aria-label="Blackjack cards with casino chips" style="background:linear-gradient(165deg,#2c4a3e,#5e6a62 50%,#d8d2c8)"></div>
      <h2 class="game-card__title">BLACKJACK</h2>
      <svg class="game-card__chev" width="10" height="16" viewBox="0 0 10 16"><path d="M2 2l6 6-6 6" fill="none" stroke="#f6a623" stroke-width="2.2"/></svg>
      <p class="game-card__text">Kestrane Baccarat is a very lucky game andeasy to play. It is the most popular card game in Asia and Kestrane Casino offers Baccarat Tables for All Players both High Stakes and Low stakes 24 hours</p>
    </article>
    <article class="game-card" style="top:631px">
      <div class="game-card__photo" role="img" aria-label="Fanned aces playing cards" style="background:linear-gradient(160deg,#1f5a5c,#6a8a8a 55%,#d8dcdc)"></div>
      <h2 class="game-card__title">SABONG CARDS</h2>
      <svg class="game-card__chev" width="10" height="16" viewBox="0 0 10 16"><path d="M2 2l6 6-6 6" fill="none" stroke="#f6a623" stroke-width="2.2"/></svg>
      <p class="game-card__text">Kestrane Baccarat is a very lucky game andeasy to play. It is the most popular card game in Asia and Kestrane Casino offers Baccarat Tables for All Players both High Stakes and Low stakes 24 hours</p>
    </article>

    <nav class="bottom-nav">
      <span class="bottom-nav__bump"></span>
      <span class="bottom-nav__item"><svg width="30" height="26" viewBox="0 0 30 26"><path fill="#f6a623" d="M15 1 1 13h4v12h7v-8h6v8h7V13h4z"/></svg></span>
      <span class="bottom-nav__item"><svg width="32" height="30" viewBox="0 0 32 30"><circle cx="10" cy="6" r="5" fill="#f6a623"/><path d="M2 28v-9a7 7 0 0 1 14 0v9z" fill="#f6a623"/><rect x="15" y="15" width="16" height="11" rx="2" fill="#f6a623" stroke="#050505" stroke-width="1.5"/><rect x="15" y="18" width="16" height="2" fill="#050505"/></svg></span>
      <span class="bottom-nav__item"></span>
      <span class="bottom-nav__item"><svg width="30" height="30" viewBox="0 0 30 30"><rect x="2" y="4" width="26" height="24" rx="3" fill="#f6a623"/><rect x="2" y="10" width="26" height="2" fill="#050505"/><path d="M9 19l4 4 8-8" fill="none" stroke="#050505" stroke-width="2.5"/></svg></span>
      <span class="bottom-nav__item"><svg width="28" height="30" viewBox="0 0 28 30"><circle cx="14" cy="9" r="7" fill="#f6a623"/><path d="M2 29c0-8 5-12 12-12s12 4 12 12z" fill="#f6a623"/><path d="M5 10a9 9 0 0 1 18 0" fill="none" stroke="#f6a623" stroke-width="2"/></svg></span>
      <span class="bottom-nav__center"><svg width="28" height="24" viewBox="0 0 28 24"><rect x="1" y="3" width="26" height="19" rx="3" fill="#f6a623"/><rect x="17" y="9" width="10" height="7" rx="2" fill="#050505"/></svg></span>
    </nav>
  </section>

</div>
</body>
</html>
```